Visitenkarten-Design für Garten- und Landschaftspflege
Nerapo Kulm setzte meine Vorstellungen absolut super um ich kann Ihn nur weiter empfehlen. vielen dank
Zielgruppe
Baumpflege, Baumfällung, Garten und Landschaftspflege meine zielgruppe sind Privatpersonen im alter von 20-100Jahren
Aufgabenstellung
Sehr geehrte Damen und Herren, die visitenkarte sollte die angaben so enthalten wie sie auf der von mir gestallteten Visitenkarten sind ( meine ist kein maß der Dinge). Ich habe mein Logo leider nur als 3.jpg Datei. Das Logo darf im Design erändert werden aber bitte nur Feinheiten ansonsten stehen ihnen alle türen offen um kreativ zu sein.
mit freundlichen Grüßen Jonas Vehmar

```html
<!DOCTYPE html>
<html lang="de">
<head>
<meta charset="utf-8">
<title>Visitenkarten Baumpflege Vehmar</title>
<link href="https://fonts.googleapis.com/css2?family=Questrial&family=Arimo:wght@400;700&display=swap" rel="stylesheet">
<style>
  :root {
    --forest: #414f16;
    --leaf-stripe: #cddf89;
    --meadow: #dfe8ae;
    --paper: #ffffff;
    --sheet: #ffffff;
  }
  * { box-sizing: border-box; margin: 0; padding: 0; }
  html, body { width: 860px; height: 1200px; overflow: hidden; background: var(--sheet); }
  .sheet { position: relative; width: 860px; height: 1200px; }

  .card {
    position: absolute; width: 306px; height: 198px;
    background: var(--paper); overflow: hidden;
    box-shadow: 2px 3px 6px rgba(0,0,0,0.18);
    color: var(--forest);
    font-family: "Arimo", Arial, sans-serif;
  }
  .card--tinted { background: var(--meadow); }
  .card--front { left: 98px; }
  .card--back { left: 435px; }
  .row-1 { top: 228px; }
  .row-2 { top: 487px; }
  .row-3 { top: 747px; }

  .stripe { position: absolute; top: 0; width: 16px; height: 100%; background: var(--leaf-stripe); }
  .card--front .stripe { right: 0; }
  .card--back .stripe { left: 0; }

  .brand {
    position: absolute; display: flex; flex-direction: column; align-items: center;
    font-family: "Questrial", sans-serif; font-weight: 400; color: var(--forest);
    text-transform: uppercase; text-align: center; line-height: 1.05;
  }
  .brand__square { background: var(--forest); margin-bottom: 6px; }
  .card--front .brand { left: 65px; width: 160px; top: 58px; font-size: 17px; letter-spacing: 1px; }
  .card--front .brand__square { width: 22px; height: 22px; margin-bottom: 10px; }
  .card--back .brand { left: 188px; width: 106px; top: 32px; font-size: 10.5px; letter-spacing: 0.5px; }
  .card--back .brand__square { width: 14px; height: 14px; }

  .services {
    position: absolute; left: 23px; top: 30px; list-style: none;
  }
  .services li::before { content: "· "; }
  .services--long { font-size: 7px; line-height: 8.7px; }
  .services--short { top: 33px; font-size: 9px; line-height: 11px; }
  .services--short .cont { padding-left: 6px; }
  .services--short .cont::before { content: ""; }

  .person { position: absolute; left: 23px; top: 124px; width: 82px; }
  .person__name { font-family: "Questrial", sans-serif; font-size: 12.5px; letter-spacing: 0.6px; white-space: nowrap; }
  .person__title { font-size: 5px; line-height: 7px; text-align: right; white-space: nowrap; }

  .contact { position: absolute; left: 161px; top: 125px; font-size: 8.5px; line-height: 11px; }
  .contact__line { display: flex; align-items: center; gap: 3px; white-space: nowrap; }
  .contact__line--indent { padding-left: 12px; }
  .contact__gap { height: 5px; }
  .icon { width: 9px; height: 9px; flex: none; }
</style>
</head>
<body>
<main class="sheet">

  <!-- Variant 1 -->
  <section class="card card--front row-1">
    <div class="brand"><span class="brand__square"></span><span>Baumpflege</span><span>Vehmar</span></div>
    <div class="stripe"></div>
  </section>
  <section class="card card--back row-1">
    <div class="stripe"></div>
    <ul class="services services--long">
      <li>Neupflanzungen</li>
      <li>Herstellung der Verkehrssicherheit von Bäumen</li>
      <li>Kronenrückschnitt (Einkürzung &amp; Kronenpflege)</li>
      <li>Prüfung von Bäumen auf Standsicherheit</li>
      <li>Fällung von Bäumen</li>
      <li>Obstbaumschnitt</li>
      <li>Wurzelstockfräsen</li>
    </ul>
    <div class="brand"><span class="brand__square"></span><span>Baumpflege</span><span>Vehmar</span></div>
    <div class="person"><p class="person__name">Jonas Vehmar</p><p class="person__title">Fachagrarwirt für Baumpflege<br>&amp; Baumsanierung</p></div>
    <div class="contact">
      <p class="contact__line"><svg class="icon" viewBox="0 0 10 10"><path d="M5 9.5 C3 6.5 2 5 2 3.6 A3 3 0 0 1 8 3.6 C8 5 7 6.5 5 9.5Z M5 2.4 A1.2 1.2 0 1 0 5 4.8 A1.2 1.2 0 1 0 5 2.4Z" fill="none" stroke="currentColor" stroke-width="0.9"/></svg>Lindenweg 7</p>
      <p class="contact__line contact__line--indent">85634 Hohenbrunn</p>
      <div class="contact__gap"></div>
      <p class="contact__line"><svg class="icon" viewBox="0 0 10 10"><rect x="3" y="1" width="4" height="8" rx="0.8" fill="currentColor"/></svg>0171 / 482 19 53</p>
      <p class="contact__line"><svg class="icon" viewBox="0 0 10 10"><rect x="0.5" y="2" width="9" height="6" fill="none" stroke="currentColor" stroke-width="0.7"/><path d="M0.5 2 L5 5.5 L9.5 2" fill="none" stroke="currentColor" stroke-width="0.7"/></svg>kontakt@baumpflege-vehmar.de</p>
      <p class="contact__line"><svg class="icon" viewBox="0 0 10 10"><circle cx="5" cy="5" r="4.3" fill="none" stroke="currentColor" stroke-width="0.7"/><ellipse cx="5" cy="5" rx="1.8" ry="4.3" fill="none" stroke="currentColor" stroke-width="0.6"/><path d="M0.7 5 H9.3 M1.5 3 H8.5 M1.5 7 H8.5" stroke="currentColor" stroke-width="0.5"/></svg>baumpflege-vehmar.de</p>
    </div>
  </section>

  <!-- Variant 2 -->
  <section class="card card--front row-2">
    <div class="brand"><span class="brand__square"></span><span>Baumpflege</span><span>Vehmar</span></div>
    <div class="stripe"></div>
  </section>
  <section class="card card--back row-2">
    <div class="stripe"></div>
    <ul class="services services--short">
      <li>Neupflanzungen</li>
      <li>Baumschnitt</li>
      <li>Herstellung der Verkehrssicherheit</li>
      <li class="cont">von Bäumen</li>
    </ul>
    <div class="brand"><span class="brand__square"></span><span>Baumpflege</span><span>Vehmar</span></div>
    <div class="person"><p class="person__name">Jonas Vehmar</p><p class="person__title">Fachagrarwirt für Baumpflege<br>&amp; Baumsanierung</p></div>
    <div class="contact">
      <p class="contact__line"><svg class="icon" viewBox="0 0 10 10"><path d="M5 9.5 C3 6.5 2 5 2 3.6 A3 3 0 0 1 8 3.6 C8 5 7 6.5 5 9.5Z M5 2.4 A1.2 1.2 0 1 0 5 4.8 A1.2 1.2 0 1 0 5 2.4Z" fill="none" stroke="currentColor" stroke-width="0.9"/></svg>Lindenweg 7</p>
      <p class="contact__line contact__line--indent">85634 Hohenbrunn</p>
      <div class="contact__gap"></div>
      <p class="contact__line"><svg class="icon" viewBox="0 0 10 10"><rect x="3" y="1" width="4" height="8" rx="0.8" fill="currentColor"/></svg>0171 / 482 19 53</p>
      <p class="contact__line"><svg class="icon" viewBox="0 0 10 10"><rect x="0.5" y="2" width="9" height="6" fill="none" stroke="currentColor" stroke-width="0.7"/><path d="M0.5 2 L5 5.5 L9.5 2" fill="none" stroke="currentColor" stroke-width="0.7"/></svg>kontakt@baumpflege-vehmar.de</p>
      <p class="contact__line"><svg class="icon" viewBox="0 0 10 10"><circle cx="5" cy="5" r="4.3" fill="none" stroke="currentColor" stroke-width="0.7"/><ellipse cx="5" cy="5" rx="1.8" ry="4.3" fill="none" stroke="currentColor" stroke-width="0.6"/><path d="M0.7 5 H9.3 M1.5 3 H8.5 M1.5 7 H8.5" stroke="currentColor" stroke-width="0.5"/></svg>baumpflege-vehmar.de</p>
    </div>
  </section>

  <!-- Variant 3 -->
  <section class="card card--front card--tinted row-3">
    <div class="brand"><span class="brand__square"></span><span>Baumpflege</span><span>Vehmar</span></div>
    <div class="stripe"></div>
  </section>
  <section class="card card--back card--tinted row-3">
    <div class="stripe"></div>
    <ul class="services services--short">
      <li>Neupflanzungen</li>
      <li>Baumschnitt</li>
      <li>Herstellung der Verkehrssicherheit</li>
      <li class="cont">von Bäumen</li>
    </ul>
    <div class="brand"><span class="brand__square"></span><span>Baumpflege</span><span>Vehmar</span></div>
    <div class="person"><p class="person__name">Jonas Vehmar</p><p class="person__title">Fachagrarwirt für Baumpflege<br>&amp; Baumsanierung</p></div>
    <div class="contact">
      <p class="contact__line"><svg class="icon" viewBox="0 0 10 10"><path d="M5 9.5 C3 6.5 2 5 2 3.6 A3 3 0 0 1 8 3.6 C8 5 7 6.5 5 9.5Z M5 2.4 A1.2 1.2 0 1 0 5 4.8 A1.2 1.2 0 1 0 5 2.4Z" fill="none" stroke="currentColor" stroke-width="0.9"/></svg>Lindenweg 7</p>
      <p class="contact__line contact__line--indent">85634 Hohenbrunn</p>
      <div class="contact__gap"></div>
      <p class="contact__line"><svg class="icon" viewBox="0 0 10 10"><rect x="3" y="1" width="4" height="8" rx="0.8" fill="currentColor"/></svg>0171 / 482 19 53</p>
      <p class="contact__line"><svg class="icon" viewBox="0 0 10 10"><rect x="0.5" y="2" width="9" height="6" fill="none" stroke="currentColor" stroke-width="0.7"/><path d="M0.5 2 L5 5.5 L9.5 2" fill="none" stroke="currentColor" stroke-width="0.7"/></svg>kontakt@baumpflege-vehmar.de</p>
      <p class="contact__line"><svg class="icon" viewBox="0 0 10 10"><circle cx="5" cy="5" r="4.3" fill="none" stroke="currentColor" stroke-width="0.7"/><ellipse cx="5" cy="5" rx="1.8" ry="4.3" fill="none" stroke="currentColor" stroke-width="0.6"/><path d="M0.7 5 H9.3 M1.5 3 H8.5 M1.5 7 H8.5" stroke="currentColor" stroke-width="0.5"/></svg>baumpflege-vehmar.de</p>
    </div>
  </section>

</main>
</body>
</html>
```